Fernhale Business Card Design

We are looking for a fresh business card design for our new logo. We would like a business card that is unique but friendly. We are in the window coverings business offering blinds, shutters and shades for homes.

Target Market(s)

Targeting the end-consumer

Industry/Entity Type

Business

Requirements
Must have
• Must have a dedicates space for a photo of our sales person. Must contain our new logo (attached).

```html
<!DOCTYPE html>
<html lang="en">
<head>
<meta charset="utf-8">
<title>Fernhale Business Card</title>
<link href="https://fonts.googleapis.com/css2?family=Montserrat:wght@400;500;700&display=swap" rel="stylesheet">
<style>
  :root {
    --backdrop: #141414;
    --card: #242424;
    --ink: #ffffff;
    --ink-soft: #e6e6e6;
    --accent: #7cc242;
    --photo-top: #3a3d38;
    --photo-bottom: #2c2e2a;
  }
  * { margin: 0; padding: 0; box-sizing: border-box; }
  html, body {
    width: 1200px; height: 900px; overflow: hidden;
    background: var(--backdrop);
    font-family: "Montserrat", sans-serif;
  }
  .canvas { position: relative; width: 1200px; height: 900px; }
  .card {
    position: absolute; left: 250px; width: 700px; height: 400px;
    background: var(--card);
    color: var(--ink);
  }
  .card--front { top: 40px; }
  .card--back { top: 470px; }

  .brand { display: flex; align-items: center; gap: 22px; }
  .brand__square {
    width: 70px; height: 70px;
    border: 4px solid var(--ink);
    border-radius: 6px;
    flex: none;
  }
  .brand__name {
    font-weight: 500; color: var(--ink);
    font-size: 62px; letter-spacing: 1px; line-height: 1;
  }

  .card--front .brand {
    position: absolute; left: 50%; top: 150px; transform: translateX(-50%);
  }
  .card--front .site {
    position: absolute; left: 0; right: 0; bottom: 48px;
    text-align: center; font-size: 15px; letter-spacing: 2px;
    color: var(--ink-soft);
  }

  .photo {
    position: absolute; left: 56px; top: 60px;
    width: 120px; height: 120px;
    border: 2px solid var(--accent);
    border-radius: 8px;
    background: linear-gradient(180deg, var(--photo-top), var(--photo-bottom));
  }
  .card--back .brand { position: absolute; left: 56px; top: 222px; gap: 14px; }
  .card--back .brand__square { width: 48px; height: 48px; border-width: 3px; }
  .card--back .brand__name { font-size: 40px; }

  .divider {
    position: absolute; left: 340px; top: 60px;
    width: 2px; height: 280px; background: var(--accent);
  }
  .contact { position: absolute; left: 366px; top: 72px; }
  .contact__name {
    font-weight: 700; color: var(--accent);
    font-size: 24px; letter-spacing: 2px; text-transform: uppercase;
    line-height: 1.2;
  }
  .contact__role { font-size: 16px; letter-spacing: 1px; margin-top: 4px; }
  .contact__address {
    font-size: 16px; letter-spacing: 1px; line-height: 1.35; margin-top: 20px;
    font-style: normal;
  }
  .contact__list { list-style: none; margin-top: 16px; }
  .contact__item {
    display: flex; align-items: center; gap: 12px;
    font-size: 16px; letter-spacing: 0.6px; line-height: 1.6;
    white-space: nowrap;
  }
  .contact__icon { width: 14px; height: 14px; fill: var(--accent); flex: none; }
  .contact__highlight { color: var(--accent); }
</style>
</head>
<body>
<main class="canvas">
  <section class="card card--front">
    <div class="brand">
      <span class="brand__square"></span>
      <span class="brand__name">Fernhale</span>
    </div>
    <p class="site">www.fernhalehome.com</p>
  </section>

  <section class="card card--back">
    <div class="photo" role="img" aria-label="Portrait photo of the sales person"></div>
    <div class="brand">
      <span class="brand__square"></span>
      <span class="brand__name">Fernhale</span>
    </div>
    <span class="divider"></span>
    <div class="contact">
      <h1 class="contact__name">Daniel Ross</h1>
      <p class="contact__role">Sales Manager</p>
      <address class="contact__address">18 Mill Lane Ardmore,<br>Scotland KA20 4PL</address>
      <ul class="contact__list">
        <li class="contact__item">
          <svg class="contact__icon" viewBox="0 0 24 24"><path d="M6.6 10.8a15.1 15.1 0 0 0 6.6 6.6l2.2-2.2a1 1 0 0 1 1-.25 11.4 11.4 0 0 0 3.6.57 1 1 0 0 1 1 1V20a1 1 0 0 1-1 1A17 17 0 0 1 3 4a1 1 0 0 1 1-1h3.5a1 1 0 0 1 1 1c0 1.25.2 2.45.57 3.57a1 1 0 0 1-.25 1z"/></svg>
          +44 (0)1632 960418
        </li>
        <li class="contact__item">
          <svg class="contact__icon" viewBox="0 0 24 24"><path d="M2 5h20v14H2z M2 5l10 8 10-8" fill="none" stroke="#7cc242" stroke-width="2.5"/></svg>
          annareid@fernhaleblinds.com
        </li>
        <li class="contact__item">
          <svg class="contact__icon" viewBox="0 0 24 24"><g fill="none" stroke="#7cc242" stroke-width="2"><circle cx="12" cy="12" r="10"/><ellipse cx="12" cy="12" rx="4.5" ry="10"/><path d="M2 12h20M4 7h16M4 17h16"/></g></svg>
          <span>www.<span class="contact__highlight">fernhaleblinds</span>.com</span>
        </li>
      </ul>
    </div>
  </section>
</main>
</body>
</html>
```